3 screens for iOS app

I need a settings screen, dashboard and leaderboard screen created for an iPhone fitness app that is nearing completion. I have the template in .psd format that needs to be adhered to for consistency, and there are wireframe sketches (literally pen & paper) that you will translate into .psd files for chopping up and adding into the app. Also I need this by Monday.

Settings Screen:

Using the template psd, I need a basic list similar to the setting screen example attached (no icons needed, just text). The list of settings in order are:
Disclaimer
Edit Profile
Feedback
Help!
Terms of Use
Privacy Policy
Push Notifications (switcher icon on/off)
Pagebook Posts (switcher icon on/off)
Chirpel Posts (switcher icon on/off)
Kelvora Vidstream Channel
Log Out

Dashboard:
The dashboard tempalte is attached. This dashboard should be inserted between the Grey banner heading and the Orange 14min standard routine bar. It will shift the graph down. The graph should remain unchanged, all you need to do in sert a cool looking dashboard inbetween the grey and orange bars

Dashboard contents:

Three dials (similar to pacemint, stridelog etc - see attached as an example) that display your progress

Dial 1: Title: Week
Dial should change colour as score approaches goal (ideally from green to orange as per icon example attached but not necessarily if you can make it look better)
Inside the dial it needs to include
Total: 598
Goal: 2,000
Days left: 5

Dial 2: Title: Improvement
Inside the dial it needs to include:
Start: 350
PB: 700
+100% in bold, centered

Dial 3: Title: Belt
Inside the dial needs to include:
Total: 9,834
Goal: 25,000

Leaderboard Screen:

Again using the template, with the grey banner heading at the top and tab bar at the bottom:

The leaderboard should be divided into two sections. The first is for my personal scores (as a user). The second section is for all players scores.

Section 1:
- Light grey background, dark grey text. Column titles can be pressed to filter columns. When pressed title changes colour from grey to orange (bold). If you can highlight two of the column titles orange that will be good

Section 2:
- White background, dark grey text. Column titles can be pressed to filter columns.
- Row height should be quite small to fit a large number of names on the screen.

Column titles: (sorry the wireframe sketch text is tough to read)
Rank / Name / W/outs / Wins / Week / Total / Belt

Rank - numeric values from 1-999
Name - text field
W/outs - number from 1-999
Wins - number 1-999
Week - number 1 - 99,999
Total - number 1- 99,999
Belt - coloured dot (white, black, red, blue, green, yellow)

For more info, refer http://www.kelvora-example.co/ and download the old app (iphone only) for an idea what we're after.

Industry/Entity Type

Fitness

Colors
f68e4e

Requirements
Must have
• Use the .psd template provided. We're not looking for a redesign.
• The fonts are:
• LeckerliOne Regular
• LobsterTwo Bold
• MeriendaOne Regular
• MVBoli
• GothamExtraLight
• LobsterTwo
Nice to have
• The best dashboard of all time.
Should not have
• changes to fonts,

```html
<!DOCTYPE html>
<html lang="en">
<head>
<meta charset="utf-8">
<title>Settings</title>
<link rel="stylesheet" href="https://fonts.googleapis.com/css2?family=Montserrat:wght@400;500;600&display=swap">
<style>
  :root {
    --slate: #3f454d;
    --slate-edge: #5b6169;
    --row-bg: #fafafa;
    --divider: #e2e3e5;
    --ink: #3a3f46;
    --accent: #f7941d;
    --muted: #8c9198;
    --white: #ffffff;
    --battery: #4cd964;
    --trend: #8fd14f;
  }
  * { box-sizing: border-box; margin: 0; padding: 0; }
  html, body {
    width: 1200px; height: 2206px; overflow: hidden;
    background: var(--row-bg);
    font-family: "Montserrat", "Helvetica Neue", Arial, sans-serif;
  }
  .app-screen { position: relative; width: 1200px; height: 2206px; overflow: hidden; }

  .status-bar {
    position: absolute; top: 0; left: 0; width: 100%; height: 82px;
    background: var(--slate); color: var(--white);
  }
  .status-bar .time {
    position: absolute; left: 0; right: 0; top: 18px; text-align: center;
    font-size: 42px; font-weight: 500;
  }
  .status-bar .signal { position: absolute; left: 20px; top: 20px; }
  .status-bar .battery { position: absolute; right: 30px; top: 24px; }

  .nav-bar {
    position: absolute; top: 82px; left: 0; width: 100%; height: 162px;
    background: var(--slate); color: var(--white);
  }
  .nav-bar .back {
    position: absolute; left: 34px; top: 50px; display: flex; align-items: center; gap: 22px;
    font-size: 54px;
  }
  .nav-bar .title {
    position: absolute; left: 0; right: 0; top: 42px; text-align: center;
    font-size: 66px; font-weight: 400;
  }

  .settings-list {
    position: absolute; top: 244px; left: 0; width: 100%; height: 1768px; overflow: hidden;
    list-style: none;
  }
  .settings-list::before {
    content: ""; position: absolute; left: 28px; top: 0; bottom: 0; width: 2px;
    background: var(--divider); z-index: 1;
  }
  .setting-row {
    position: relative; height: 190px; border-bottom: 2px solid var(--divider);
    display: flex; align-items: center; justify-content: space-between;
    padding: 0 52px 0 116px; font-size: 48px; color: var(--ink); background: var(--row-bg);
  }
  .setting-row.is-active {
    background: var(--slate); color: var(--white); height: 170px; border-bottom: none;
  }
  .setting-row.is-active::before {
    content: ""; position: absolute; left: 0; top: 0; bottom: 0; width: 28px;
    background: var(--accent); z-index: 2;
  }

  .toggle {
    position: relative; width: 190px; height: 112px; border-radius: 56px; background: var(--slate);
  }
  .toggle::after {
    content: ""; position: absolute; top: 12px; left: 12px; width: 88px; height: 88px;
    border-radius: 50%; background: var(--white);
  }
  .toggle.is-on { background: var(--accent); }
  .toggle.is-on::after { left: 90px; }

  .tab-bar {
    position: absolute; left: 0; bottom: 0; width: 100%; height: 194px; background: var(--slate);
  }
  .tab {
    position: absolute; bottom: 0; width: 220px; height: 194px; margin-left: -110px;
    display: flex; flex-direction: column; align-items: center; justify-content: flex-end;
    padding-bottom: 14px; color: var(--muted); font-size: 36px;
  }
  .tab svg { margin-bottom: 14px; }
  .tab.is-current { color: var(--white); }
  .tab-start {
    position: absolute; left: 450px; top: -42px; width: 300px; height: 300px; border-radius: 50%;
    background: var(--slate); border: 5px solid var(--slate-edge);
  }
  .tab-start-label {
    position: absolute; left: 0; right: 0; bottom: 14px; text-align: center; color: var(--muted); font-size: 38px;
  }
</style>
</head>
<body>
<div class="app-screen">

  <header class="status-bar">
    <svg class="signal" width="230" height="44" viewBox="0 0 230 44" aria-hidden="true">
      <g fill="#fff">
        <circle cx="14" cy="22" r="10"/><circle cx="40" cy="22" r="10"/><circle cx="66" cy="22" r="10"/>
        <circle cx="92" cy="22" r="10"/><circle cx="118" cy="22" r="10"/>
      </g>
      <g fill="none" stroke="#fff" stroke-width="5" stroke-linecap="round">
        <path d="M142 16 a30 30 0 0 1 44 0"/><path d="M150 24 a19 19 0 0 1 28 0"/>
      </g>
      <circle cx="164" cy="33" r="5" fill="#fff"/>
    </svg>
    <div class="time">9:00 AM</div>
    <svg class="battery" width="92" height="40" viewBox="0 0 92 40" aria-hidden="true">
      <rect x="2" y="2" width="80" height="36" rx="5" fill="none" stroke="#fff" stroke-width="3"/>
      <rect x="7" y="7" width="70" height="26" rx="2" fill="var(--battery)"/>
      <rect x="84" y="13" width="6" height="14" rx="2" fill="#fff"/>
    </svg>
  </header>

  <nav class="nav-bar">
    <div class="back">
      <svg width="30" height="56" viewBox="0 0 30 56" aria-hidden="true">
        <path d="M26 4 L5 28 L26 52" fill="none" stroke="#fff" stroke-width="5" stroke-linecap="round" stroke-linejoin="round"/>
      </svg>
      <span>Back</span>
    </div>
    <h1 class="title">Settings</h1>
  </nav>

  <ul class="settings-list">
    <li class="setting-row">Disclaimer</li>
    <li class="setting-row">Edit Profile</li>
    <li class="setting-row">Feedback</li>
    <li class="setting-row is-active">Help!
      <svg width="22" height="36" viewBox="0 0 22 36" aria-hidden="true">
        <path d="M4 4 L18 18 L4 32" fill="none" stroke="#fff" stroke-width="5" stroke-linecap="round" stroke-linejoin="round"/>
      </svg>
    </li>
    <li class="setting-row">Terms of Use</li>
    <li class="setting-row">Privacy Policy</li>
    <li class="setting-row">Push Notifications <span class="toggle is-on"></span></li>
    <li class="setting-row">Pagebook Posts <span class="toggle"></span></li>
    <li class="setting-row">Chirpel Posts <span class="toggle"></span></li>
  </ul>

  <footer class="tab-bar">
    <div class="tab" style="left:110px">
      <svg width="90" height="96" viewBox="0 0 90 96" aria-hidden="true">
        <g fill="none" stroke="currentColor" stroke-width="4">
          <ellipse cx="45" cy="30" rx="20" ry="25"/>
          <path d="M6 94 C6 66 22 58 45 58 C68 58 84 66 84 94 Z"/>
        </g>
      </svg>
      <span>Profile</span>
    </div>
    <div class="tab is-current" style="left:311px">
      <svg width="110" height="90" viewBox="0 0 110 90" aria-hidden="true">
        <path d="M6 80 L34 46 L50 60 L78 22 L104 8" fill="none" stroke="var(--trend)" stroke-width="6" stroke-linejoin="round" stroke-linecap="round"/>
        <path d="M6 70 L34 36 L50 50 L78 12" fill="none" stroke="var(--trend)" stroke-width="3" stroke-linecap="round" opacity=".7"/>
      </svg>
      <span>Results</span>
    </div>
    <div class="tab-start">
      <svg width="110" height="110" viewBox="0 0 110 110" style="position:absolute;left:100px;top:48px" aria-hidden="true">
        <path d="M22 8 L98 55 L22 102 Z" fill="var(--muted)"/>
      </svg>
    </div>
    <div class="tab-start-label" style="left:450px;width:300px;right:auto">Start</div>
    <div class="tab" style="left:878px">
      <svg width="90" height="110" viewBox="0 0 90 110" aria-hidden="true">
        <path d="M28 54 L12 100 L30 92 L38 108 L48 68 M62 54 L78 100 L60 92 L52 108 L44 68" fill="none" stroke="currentColor" stroke-width="4" stroke-linejoin="round"/>
        <circle cx="45" cy="38" r="32" fill="var(--accent)"/>
        <text x="45" y="52" text-anchor="middle" font-family="Montserrat, sans-serif" font-size="38" font-weight="600" fill="#fff">2</text>
      </svg>
      <span>Challenges</span>
    </div>
    <div class="tab" style="left:1087px">
      <svg width="100" height="96" viewBox="0 0 100 96" aria-hidden="true">
        <path d="M20 92 L14 52 C12 30 18 12 34 6 L52 4 L56 14 L44 22 L48 34 C60 24 80 26 90 40 C96 56 90 80 70 90 Z" fill="none" stroke="currentColor" stroke-width="4" stroke-linejoin="round"/>
      </svg>
      <span>Routines</span>
    </div>
  </footer>

</div>
</body>
</html>
```